creation of a business card design for a company specializing in the creation...

I would like to create a design for a professional business card on a black background and with the company's colors (I am attaching some files: including the logo in horizontal and centered format, I am also attaching a recent project design a T-shirt, this is the one I chose to give you an idea of my preferences.

we are in the process of developing a new website design, it is still in the development phase but it can be viewed at the following address: www.vantrelmo.be to give you other ideas about the company
you will see for yourself the subject of my main activity: company specializing in the construction of stairs

I would like a business card that stands out from the rest with a unique design

here is the informations
Name: Lucien Barthel
Function: Manager
Address: Rue Moulinet du Parc 42
7180 Montferlan
telephone: +32 468 219 804
email: info@rx7p.be
website: rx7p. be
social networks: Facebook, YouTube, TikTok, Instagram

Target Market(s)

customer who wants to have a beautiful staircase built

Industry/Entity Type

contruction d'escalier

Contact Information for Business Card

Adresse. Numero de telephone, site web, le texte : "Createur d'escalier", logo recto-verso, icone des reseaux sociaux

Requirements
Must have
• the mention: Stair creator
Nice to have
• an illustration of a designer staircase
Should not have
• do not distort the logo

```html
<!DOCTYPE html>
<html lang="fr">
<head>
<meta charset="utf-8">
<title>RX7P – Cartes de visite</title>
<link href="https://fonts.googleapis.com/css2?family=Lato:wght@400;700;900&display=swap" rel="stylesheet">
<style>
  :root {
    --backdrop: #1d1c1d;
    --card: #262627;
    --card-edge: #7aa9c9;
    --steel-blue: #4f7fa3;
    --sky-blue: #9cc2dd;
    --text-light: #d9dde0;
    --text-white: #ffffff;
  }
  * { margin: 0; padding: 0; box-sizing: border-box; }
  html, body { width: 1200px; height: 939px; overflow: hidden; background: var(--backdrop); }
  body { position: relative; font-family: "Lato", sans-serif; }

  .card {
    position: absolute;
    width: 580px;
    height: 330px;
    background: var(--card);
    border-radius: 18px;
    box-shadow: 0 4px 0 var(--card-edge), 0 18px 40px rgba(0,0,0,.55);
    overflow: hidden;
  }
  .card--front { left: 110px; top: 100px; }
  .card--back  { left: 510px; top: 500px; }

  .stair-art {
    position: absolute;
    top: 0; right: 0;
    width: 100%; height: 100%;
  }

  .brand {
    position: absolute;
    display: flex;
    align-items: center;
    gap: 14px;
    color: var(--text-white);
    font-weight: 900;
    letter-spacing: 6px;
  }
  .brand__mark {
    width: 34px; height: 34px;
    background: var(--sky-blue);
  }
  .card--front .brand { left: 70px; top: 190px; font-size: 64px; }
  .card--back .brand { left: 56px; top: 56px; font-size: 42px; }
  .card--back .brand__mark { width: 24px; height: 24px; }

  .person { position: absolute; left: 60px; top: 150px; }
  .person__name {
    color: var(--steel-blue);
    font-weight: 900;
    font-size: 26px;
    letter-spacing: .5px;
    text-transform: uppercase;
  }
  .person__role {
    color: var(--sky-blue);
    font-size: 17px;
    margin-top: 2px;
  }

  .contact-list {
    position: absolute;
    left: 60px; top: 232px;
    list-style: none;
    color: var(--text-light);
    font-size: 15px;
    line-height: 26px;
  }
  .contact-list li,
  .address { display: flex; align-items: center; gap: 12px; }
  .contact-list svg,
  .address svg { width: 13px; height: 13px; fill: var(--steel-blue); flex: none; }

  .address {
    position: absolute;
    left: 285px; top: 232px;
    align-items: flex-start;
    color: var(--text-light);
    font-size: 15px;
    line-height: 24px;
    white-space: nowrap;
  }
  .address svg { margin-top: 5px; }
</style>
</head>
<body>

  <section class="card card--front">
    <svg class="stair-art" viewBox="0 0 580 330" role="img" aria-label="Illustration d'un escalier flottant en marches bleues">
      <defs>
        <linearGradient id="stairFront" x1="0" y1="0" x2="1" y2="1">
          <stop offset="0" stop-color="#9cc2dd"/>
          <stop offset="1" stop-color="#4f7fa3"/>
        </linearGradient>
      </defs>
      <polygon points="250,0 420,0 580,170 580,330 500,330 470,220 330,70 250,40" fill="url(#stairFront)"/>
    </svg>
    <div class="brand"><span class="brand__mark"></span>RX7P</div>
  </section>

  <section class="card card--back">
    <svg class="stair-art" viewBox="0 0 580 330" role="img" aria-label="Illustration d'un escalier flottant en marches bleues">
      <defs>
        <linearGradient id="stairBack" x1="0" y1="0" x2="1" y2="1">
          <stop offset="0" stop-color="#9cc2dd"/>
          <stop offset="1" stop-color="#4f7fa3"/>
        </linearGradient>
      </defs>
      <polygon points="300,0 460,0 580,140 580,300 540,300 500,200 380,60 300,30" fill="url(#stairBack)"/>
    </svg>

    <div class="brand"><span class="brand__mark"></span>RX7P</div>

    <div class="person">
      <p class="person__name">Lucien Barthel</p>
      <p class="person__role">Créateur d'escalier</p>
    </div>

    <ul class="contact-list">
      <li>
        <svg viewBox="0 0 24 24"><path d="M6.6 10.8a15.1 15.1 0 0 0 6.6 6.6l2.2-2.2a1 1 0 0 1 1-.25 11.4 11.4 0 0 0 3.6.57 1 1 0 0 1 1 1V20a1 1 0 0 1-1 1A17 17 0 0 1 3 4a1 1 0 0 1 1-1h3.5a1 1 0 0 1 1 1c0 1.25.2 2.45.57 3.6a1 1 0 0 1-.25 1z"/></svg>
        +32 468 219 804
      </li>
      <li>
        <svg viewBox="0 0 24 24"><path d="M2 5h20v14H2z M2 5l10 8 10-8" /></svg>
        info@rx7p.be
      </li>
      <li>
        <svg viewBox="0 0 24 24"><circle cx="12" cy="12" r="10"/></svg>
        rx7p.be
      </li>
    </ul>

    <div class="address">
      <svg viewBox="0 0 24 24"><path d="M12 2a7 7 0 0 0-7 7c0 5 7 13 7 13s7-8 7-13a7 7 0 0 0-7-7zm0 9.5A2.5 2.5 0 1 1 12 6.5a2.5 2.5 0 0 1 0 5z"/></svg>
      <p>Rue Moulinet du Parc 42<br>7180 Montferlan</p>
    </div>
  </section>

</body>
</html>
```